Flat bootstrap design for existing site

I'm looking for a modern flat design based around an existing logo. This has to be a custom design (no external templates), and implemented into a bootstrap framework.

The logo is attached as 2 versions - choose whichever you want, that flows better with whatever design you choose.

Added screenshots of the existing site (currently using the default bootstrap layouts). Please make your designs around those pages in the screenshots (i.e. the homepage only has the postal code input and the header). The active page has 3 screenshots, because I wanted to illustrate the other states that would be visible (in the table rows).

This is a moving/junk removal website, just for some context.

Here's some example websites (flat designs) that I like, just to give you an idea of what I'm after.

https://www.plimvora.com/
https://dacklow.com/
https://trevanu.com/
https://quobrintal.com/en/

Coding

Coded - Design and coding required

Number of Pages Required

5+ page

Colors

Designer to choose colors to be used in the design.

Requirements
Must have
• It must be a modern/simple flat design, that is built around the existing logo (attached).
• It has to be implemented using bootstrap.

```html
<!DOCTYPE html>
<html lang="en">
<head>
<meta charset="utf-8">
<title>Bravlo – Booking Details</title>
<link href="https://fonts.googleapis.com/css2?family=Raleway:wght@400;500;600;700;800&display=swap" rel="stylesheet">
<style>
:root{
  --sky:#4ac9f5;
  --teal:#1d82a8;
  --panel:#f1f0ee;
  --panel-border:#d9d9d9;
  --ink:#222;
  --muted:#555;
  --line:#d6e4ee;
  --pending:#e8503e;
  --nav-active:#6f6f6f;
  --footer:#000;
}
*{box-sizing:border-box;margin:0;padding:0}
html,body{width:1168px;height:1200px;overflow:hidden;background:#fff;font-family:"Raleway",sans-serif;color:var(--ink)}
.site-header{position:absolute;left:0;top:0;width:1168px;height:97px;background:var(--sky)}
.brand{position:absolute;left:84px;top:27px;color:#fff;font-weight:800;font-size:36px;letter-spacing:1px;display:flex;align-items:center;gap:10px}
.brand-mark{width:26px;height:26px;border-radius:50%;background:#fff;display:inline-block}
.main-nav{position:absolute;top:34px;right:84px;display:flex;gap:8px}
.main-nav a{color:#fff;text-decoration:none;font-size:14px;font-weight:500;padding:0 19px;height:28px;line-height:28px;display:block}
.main-nav a.active{background:var(--nav-active);border-radius:2px;box-shadow:0 1px 3px rgba(0,0,0,.35)}
.panel{position:absolute;left:84px;width:999px;background:var(--panel);border:1px solid var(--panel-border)}
.booking{top:116px;height:455px}
.drivers{top:603px;height:429px}
.panel-title{position:absolute;left:25px;top:35px;font-size:23px;font-weight:500}
.panel-rule{position:absolute;left:21px;top:78px;width:958px;border-top:1px solid #dedede}
.field-label{position:absolute;font-size:18px;font-weight:500}
.field{position:absolute;background:#fff;border:1px solid #cfcfcf;height:48px;padding:0 24px;font-size:13px;text-transform:uppercase;color:var(--muted);display:flex;align-items:center;justify-content:space-between;letter-spacing:.3px}
.field.textarea{height:91px;align-items:flex-start;padding-top:17px}
.resize{position:absolute;right:12px;bottom:18px}
.btn-update{position:absolute;left:827px;top:365px;width:152px;height:49px;background:var(--sky);color:#fff;border:0;font-family:inherit;font-size:19px;font-weight:500}
.notice{position:absolute;left:21px;top:90px;width:956px;height:48px;background:var(--sky);color:#fff;font-size:13px;padding:0 21px;line-height:48px}
.driver-table{position:absolute;left:22px;top:145px;width:954px;border-collapse:collapse;border:1px solid #b9cfdf;background:#fff;font-size:13px}
.driver-table th{background:var(--teal);color:#fff;font-weight:500;text-align:left;height:42px;padding:10px 24px 0;border-right:1px solid #2f6f8d}
.driver-table th:last-child{border-right:0}
.driver-table td{height:38px;padding:0 24px;border-top:1px solid var(--line);border-right:1px solid var(--line);color:var(--muted)}
.driver-table td:last-child{border-right:0;text-align:center}
.driver-table tr.empty td{height:41px}
.col-name{width:125px}.col-dist{width:215px}.col-time{width:146px}
.badge-pending{display:inline-block;width:103px;height:26px;line-height:26px;background:var(--pending);color:#fff;font-size:13px;position:relative;left:-4px;top:-2px}
.site-footer{position:absolute;left:0;top:1113px;width:1168px;height:87px;background:var(--footer);color:#fff}
.copyright{position:absolute;left:84px;top:34px;font-size:13px}
.social{position:absolute;left:945px;top:32px;display:flex;gap:6px}
.social span{width:23px;height:23px;border-radius:50%;display:block}
</style>
</head>
<body>
<header class="site-header">
  <div class="brand"><span class="brand-mark"></span>BRAVLO</div>
  <nav class="main-nav">
    <a class="active" href="#">BOOK</a>
    <a href="#">HOW IT WORKS</a>
    <a href="#">BECOME A DRIVER</a>
    <a href="#">SIGN IN</a>
  </nav>
</header>

<section class="panel booking">
  <h2 class="panel-title">Booking Details</h2>
  <div class="panel-rule"></div>
  <label class="field-label" style="left:24px;top:112px">Package selected:</label>
  <label class="field-label" style="left:510px;top:112px">Pick-up time selected:</label>
  <div class="field" style="left:21px;top:150px;width:470px">
    <span>Package 1</span>
    <svg width="9" height="12" viewBox="0 0 9 12"><path d="M4.5 0L9 5H0z M4.5 12L0 7h9z" fill="#222"/></svg>
  </div>
  <div class="field" style="left:507px;top:150px;width:469px">
    <span>July 18 at 0:13 AM</span>
    <svg width="13" height="13" viewBox="0 0 13 13"><rect x="0.5" y="1.5" width="12" height="11" fill="none" stroke="#333"/><rect x="0.5" y="1.5" width="12" height="3" fill="#333"/><path d="M3 0v3M10 0v3M4.5 4.5v8M8.5 4.5v8M0.5 7.5h12M0.5 10h12" stroke="#333"/></svg>
  </div>
  <label class="field-label" style="left:24px;top:218px">Description:</label>
  <div class="field textarea" style="left:21px;top:257px;width:956px">
    <span>Package 1</span>
    <svg class="resize" width="12" height="12" viewBox="0 0 12 12"><path d="M1 11L11 1M7 1h4v4M1 7v4h4" stroke="#888" fill="none" stroke-width="1.5"/></svg>
  </div>
  <button class="btn-update">Update</button>
</section>

<section class="panel drivers">
  <h2 class="panel-title">Drivers in your area</h2>
  <div class="panel-rule"></div>
  <div class="notice">Please stay on this page and be patient, while we contact the drivers and find you one ASAP.</div>
  <table class="driver-table">
    <thead>
      <tr><th class="col-name">Name</th><th class="col-dist">Distance (km)</th><th class="col-time">Agreed pick-up time</th><th></th></tr>
    </thead>
    <tbody>
      <tr><td>Dale Marsh</td><td>4.04km away</td><td>-</td><td><span class="badge-pending">Pending</span></td></tr>
      <tr><td>Owen Pryce</td><td>5.7km away</td><td>_</td><td><span class="badge-pending">Pending</span></td></tr>
      <tr><td>Elliot Varne</td><td>11.13km away</td><td>_</td><td><span class="badge-pending">Pending</span></td></tr>
      <tr><td>Victor Hallam</td><td>11.91km away</td><td>_</td><td><span class="badge-pending">Pending</span></td></tr>
      <tr class="empty"><td></td><td></td><td></td><td></td></tr>
    </tbody>
  </table>
</section>

<footer class="site-footer">
  <p class="copyright">2017 © Bravlo. All rights reserved.</p>
  <div class="social" aria-label="Social links">
    <span style="background:#3b5b9a"></span>
    <span style="background:#2aa3e0"></span>
    <span style="background:#e5402f"></span>
    <span style="background:#c8231d"></span>
    <span style="background:#c2377f"></span>
  </div>
</footer>
</body>
</html>
```